Uncoded front page web design for wedding and event planning company

Hi.

I am launching a wedding and event planning company called Silver Fern Celebrations and need a professional and appealing web design.

So, let me explain my company. I am based in Swindon in Wiltshire but the company will plan weddings and events in Oxfordshire, Wiltshire, Berkshire and London.

We will plan weddings, birthdays, conferences, product launches, fashion shows and conventions but the main focus of the website at this stage should be the weddings with all the other occasions being covered under a single 'events' heading.

My contact details for the website should be:
Maureen Hollis
maureen@silverferncelebrations.co.uk
01632 960418 / 07700 900627

I'd like the website to feel clean, bright and elegant and be set against a white or off-white background. My logo is purple and I'd therefore like some purple incorporated into the design although feel free to use a more muted purple as my one might be a little bright? I'm also considering whether it would look nice paired with a little of the colour gold - maybe as a font colour in places?? I'll leave you to figure that one out as your design eye will be better than mine but for your reference below is my purple colour and my suggested gold one....

My purple colour is Pantone 2592 C but feel free to use others
My suggested gold I'm looking at is Pantone 14-1041 TCX

I would like to incorporate a Facebook feed in the front page if possible, if it looks right. I'd also like to include a variety of pictures as well so I've included a few in a Dropbox folder which is linked below. Please don't feel obliged to use them all by any means (there's loads!) but you've got a few there to play with. If you find any other royalty free images you'd rather use please go ahead but on the understanding I can have them afterwards!

My logo can be retrieved via this Dropbox link...
You'll notice there are 2 styles of placement. Please feel free to use either to fit in with your design...
https://www.filevault.example/sh/kq8pw2mzr4tn7ab/BBBQrt6hNxyvpe5L81GmsWd3Pc?dl=0

The wedding images I have are in this Dropbox folder...
https://www.filevault.example/sh/m9vc2xh6pl1qw8j/BBB4zkrNvLpte6P57YhaJoscb?dl=0

Other than that, it's over to you.... I can't wait to receive your designs :-)

Ooh....finally just to say, as I receive designs in I think I'll notice aspects that I like and don't like and if I feel they'll be useful for other designers, I'll update my brief below. Thanks

BRIEF UPDATE:
Someone asked if I had a tag-line. Could you use "Creating exquisite occasions today for amazing memories tomorrow"

I realise I hadn't explained what I'd like included on my home page so here's some notes to consider....

A welcome to section for me to start narrative about us and our services which has a button that links to our 'about us' page and 'services' page for further information.

A section that nicely illustrates what services we offer whether that be with icons or pictures.

A section with some photos in that would link to our gallery

A section that shows some customer reviews and blog entries that would link to my reviews page and blog to read more.

And finally a contact us section with my details, social media links and site map.

***
I also need to draw attention to where in the UK my services cover. I was therefore thinking perhaps we could use a picture to demonstrate this where it highlights Wiltshire, Oxfordshire, Berkshire and London on a map thereby demonstrating our areas covered. I have found several English county maps when searching on Google but I'm not sure how to highlight the areas I cover (or dull out the areas I don't) so if you have any ideas on this, I'd really like it incorporated. Thanks. (by the way, for those of you not familiar with English counties, the ones I cover are often abbreviated to Wilts, Oxon, Berks, London, so if you find a suitable map with those names on rather than the full names, you'll know what they are!)

I've found an image of the county map which might work well. I was wondering whether we might somehow grey out the counties I don't cover and just keep the ones I do as mentioned above and then crop it into perhaps a shadowed circle? I've attached a screenshot to the brief.

I've decided on the tag-line "Creating exquisite occasions today for amazing memories tomorrow" so if that could be included somewhere that would be great. I also need to draw attention to where in the UK my services cover. I was therefore thinking perhaps we could use a picture to demonstrate this where it highlights Wiltshire, Oxfordshire, Berkshire and London on a map thereby demonstrating our areas covered. I have found several English county maps when searching on Google but I'm not sure how to highlight the areas I cover (or dull out the areas I don't) so if you have any ideas on this, I'd really like it incorporated. Thanks. Added Wednesday, June 24, 2015

Target Market(s)

Predominately women aged 25-55

Industry/Entity Type

Wedding Planner

Number of Pages Required

1 page

Font styles to use
Sans Serif
Script

Requirements
Nice to have
• I'd like to see how the colour theme of purple and perhaps a little gold (maybe as a font colour) look against a white background. I've mentioned the Pantone colours in the brief above.
• I've attached a screenshot of a webpage with gold writing in and fonts that I like. Perhaps it could give you inspiration?
Should not have
• I really don't like the font SCRIPTINA so please done use that.

```html
<!DOCTYPE html>
<html lang="en">
<head>
<meta charset="utf-8">
<title>Silver Fern Celebrations</title>
<link href="https://fonts.googleapis.com/css2?family=Great+Vibes&family=Open+Sans:wght@400;600;700&display=swap" rel="stylesheet">
<style>
:root{
  --purple:#8b1a8e;
  --purple-soft:#a64aa8;
  --gold:#d4a659;
  --gold-dark:#c18f3e;
  --ink:#555;
  --ink-soft:#777;
  --light:#f7f7f7;
  --line:#e4e0dc;
  --footer:#ebeaea;
  --white:#fff;
}
*{margin:0;padding:0;box-sizing:border-box}
html,body{width:688px;height:1200px;overflow:hidden;background:var(--white)}
body{font-family:"Open Sans",sans-serif;color:var(--ink);position:relative}
.abs{position:absolute}
.script{font-family:"Great Vibes",cursive;font-weight:400}

/* header */
.site-header{top:0;left:0;width:688px;height:49px;background:linear-gradient(#fff 60%,#f1eef2)}
.brand{left:110px;top:16px;display:flex;align-items:center;gap:5px;color:var(--purple);font-size:10.5px;font-weight:600;letter-spacing:.2px;white-space:nowrap}
.brand-dot{width:16px;height:16px;border-radius:50%;background:var(--purple)}
.main-nav{left:301px;top:17px;display:flex;gap:14px;font-size:11px;color:#666;white-space:nowrap}
.main-nav .sep{color:#aaa}
.main-nav .active{color:var(--purple);font-weight:600}

/* hero */
.hero{top:49px;left:0;width:688px;height:266px;background:linear-gradient(100deg,#c9d3dc 0%,#2b3a5c 22%,#223253 40%,#e9e4e2 58%,#f5f2f0 75%,#d8d0cc 100%)}
.hero-caption{left:41px;top:120px;width:282px;height:132px;background:rgba(40,40,40,.65);color:#fff;text-align:center}
.hero-caption h1{font-size:25px;line-height:22px;margin:16px 10px 0;text-align:left;padding-left:5px}
.hero-caption p{font-size:5.6px;line-height:7px;margin:6px 14px 0}
.btn-outline{display:inline-block;margin-top:11px;border:1.5px solid var(--gold);color:var(--gold);font-size:7.5px;font-weight:700;padding:4px 6px;letter-spacing:.3px}
.hero-arrow{top:170px;color:#fff;font-size:28px;font-weight:600}
.hero-tab{left:0;top:290px}
.dots{left:323px;top:299px;display:flex;gap:8px}
.dots span{width:9px;height:9px;border-radius:50%;background:#e8d4ac}
.dots .on{background:var(--purple)}

/* gallery strip */
.gallery{top:322px;left:0;display:flex;gap:2.5px}
.gallery div{width:74px;height:74px}

/* welcome */
.welcome{top:403px;left:0;width:688px;height:137px;background:var(--light);text-align:center;border-top:1px solid #eee;border-bottom:1px solid #eee}
.section-title{font-size:28px;color:var(--gold)}
.welcome .section-title{margin-top:8px;color:#6a6a6a}
.welcome .section-title em{font-style:normal;color:var(--gold)}
.welcome p{font-size:7.3px;line-height:12.5px;width:400px;margin:4px auto 0}
.btn{display:inline-block;background:var(--gold);color:#fff;font-size:7.3px;font-weight:700;letter-spacing:.4px;padding:6px 11px;border-radius:1px}
.welcome .btn{margin-top:16px}

.ornament{display:block;margin:0 auto}

/* services */
.services{top:540px;left:0;width:688px;height:268px;text-align:center}
.services .section-title{margin-top:8px}
.services .intro{font-size:5.7px;font-style:italic;line-height:7px;width:300px;margin:6px auto 0}
.service{position:absolute;top:82px;width:110px;text-align:center}
.service-photo{width:86px;height:86px;border-radius:50%;border:4px solid #e5dccf;margin:0 auto}
.service h3{font-size:15px;color:var(--purple);margin-top:4px}
.service p{font-size:6.2px;line-height:7.5px;color:var(--ink-soft);margin-top:4px}
.services .btn{position:absolute;left:313px;top:230px}

/* blog */
.blog{top:808px;left:0;width:688px;height:269px;background:var(--light);text-align:center}
.blog .section-title{margin-top:8px}
.post{position:absolute;top:58px;width:112px;height:152px;background:#fff;border-top:2px solid #e8d3b0;text-align:left}
.post-photo{position:relative;width:108px;height:72px;margin:2px}
.date{position:absolute;left:0;top:23px;width:30px;height:30px;background:var(--purple-soft);color:#fff;text-align:left;padding-left:3px}
.date b{display:block;font-size:14px;font-weight:400;line-height:16px}
.date i{display:block;font-size:4.5px;font-style:normal}
.post h4{font-family:"Great Vibes",cursive;font-weight:400;font-size:10.5px;line-height:9px;color:#333;margin:6px 4px 0}
.post .meta{font-size:4.3px;color:var(--gold);font-style:italic;margin:3px 4px 0}
.post p{font-size:5px;line-height:6.5px;color:var(--ink-soft);margin:2px 4px 0}
.read{position:absolute;right:4px;bottom:8px;font-size:5px;color:var(--purple);display:flex;align-items:center;gap:2px}
.read span{width:5px;height:5px;border-radius:50%;background:var(--purple)}
.blog .btn{position:absolute;left:313px;top:224px}

/* footer */
.site-footer{top:1077px;left:0;width:688px;height:123px;background:var(--footer);border-top:2px solid var(--gold)}
.f-col{position:absolute;top:15px}
.f-col h5{font-size:7px;font-weight:700;color:var(--purple);display:flex;align-items:center;gap:4px}
.f-col h5 svg{width:11px;height:6px}
.f-brand{color:var(--purple);font-size:8.5px;font-weight:600;margin-top:10px;display:flex;gap:4px;align-items:center;white-space:nowrap}
.f-brand span{width:12px;height:12px;border-radius:50%;background:var(--purple)}
.f-about p{font-size:5px;line-height:7px;width:102px;text-align:justify;margin-top:7px;color:#444}
.f-links{list-style:none;font-size:6px;line-height:12.4px;margin-top:10px;padding-left:14px;color:#333}
.f-info li{list-style:none;display:flex;gap:7px;font-size:5.8px;line-height:7px;color:#444;margin-top:8px;white-space:nowrap}
.f-info svg{width:7px;height:7px;flex:none;margin-top:1px}
.social{display:flex;gap:5px;margin-top:15px;padding-left:15px}
.social span{width:11px;height:11px;border-radius:2px;background:var(--purple-soft)}
.copyright{font-size:4.8px;line-height:8px;text-align:center;margin-top:22px;color:#444}
</style>
</head>
<body>

<header class="site-header abs">
  <div class="brand abs"><span class="brand-dot"></span>Silver Fern Celebrations</div>
  <nav class="main-nav abs">
    <span class="active">Home</span><span class="sep">/</span>
    <span>About</span><span class="sep">/</span>
    <span>Services</span><span class="sep">/</span>
    <span>Blog</span><span class="sep">/</span>
    <span>Contact</span>
  </nav>
</header>

<section class="hero abs" role="img" aria-label="Bride in a white dress signing the wedding register beside the groom, bouquet in soft focus">
</section>
<div class="hero-caption abs">
  <h1 class="script">Creating exquisite occasions today for amazing memories tomorrow</h1>
  <p>Etiamursus leo vel metus. Nulla facilisi. Aec eros. Vestibulum ante ipsu primis in faucibus orci luctus et trices posuere cubilia Suspendisse sollici. Scelerisque</p>
  <span class="btn-outline">LEARN MORE</span>
</div>
<div class="hero-arrow abs" style="left:14px">&#8249;</div>
<div class="hero-arrow abs" style="left:659px">&#8250;</div>
<svg class="hero-tab abs" width="688" height="26" viewBox="0 0 688 26"><path d="M214 0H474L480 26H208Z" fill="#fff"/></svg>
<div class="dots abs"><span></span><span class="on"></span><span></span></div>

<div class="gallery abs">
  <div role="img" aria-label="Hands holding wedding rings" style="background:linear-gradient(135deg,#e8ddd6,#c9b3a6)"></div>
  <div role="img" aria-label="Bride holding bouquet" style="background:linear-gradient(135deg,#f3f1ee,#9a7d6e)"></div>
  <div role="img" aria-label="Lacing a wedding dress" style="background:linear-gradient(135deg,#d6cec6,#f4f1ed)"></div>
  <div role="img" aria-label="Glasses on a dining table" style="background:linear-gradient(135deg,#b07a48,#e6d3bb)"></div>
  <div role="img" aria-label="Table set with flowers" style="background:linear-gradient(135deg,#c7cbbf,#eceae4)"></div>
  <div role="img" aria-label="Gold rings with roses" style="background:linear-gradient(135deg,#f6f1e8,#e6c7b9)"></div>
  <div role="img" aria-label="Flower girl in a garden" style="background:linear-gradient(135deg,#7f9a62,#e8e6e0)"></div>
  <div role="img" aria-label="Waiters serving plates" style="background:linear-gradient(135deg,#e3dcd2,#8b8575)"></div>
  <div role="img" aria-label="Banquet hall with purple lighting" style="background:linear-gradient(135deg,#5c3a7e,#c9b6d8)"></div>
</div>

<section class="welcome abs">
  <h2 class="section-title script">Welcome to <em>Silver Fern</em></h2>
  <p>Lorem ipsum dolor sit amet, consectetur adipisicing elit, sed do eiusmod tempor incididunt ut labore et dolore magna aliqua. Ut enim ad minim veniam, quis nostrud exercitation ullamco laboris nisi ut aliquip commodo consequat. Duis aute irure dolor in reprehenderit in voluptate velit esse cillum dolore eu cupidatat non prdeser</p>
  <span class="btn">A BOUT US</span>
</section>

<section class="services abs">
  <h2 class="section-title script">Our services</h2>
  <svg class="ornament" width="92" height="6" viewBox="0 0 92 6"><path d="M0 3H36M56 3H92" stroke="#d8d4cf"/><circle cx="42" cy="3" r="2" fill="none" stroke="#bbb"/><circle cx="50" cy="3" r="2" fill="none" stroke="#bbb"/></svg>
  <p class="intro">Lorem ipsum dolor sit amet, consectetur adipisicing elit, sed do eiusmod tempor incididunt ut labore et dolore magna aliqua. Ut enim ad minim veniam, quis nostrud exercitation ullamco</p>
  <div class="service" style="left:96px"><div class="service-photo" role="img" aria-label="Groom placing a ring on the bride's hand" style="background:radial-gradient(circle at 40% 40%,#e7c7b5,#8fcf4a)"></div><h3 class="script">Wedding Planning</h3><p>Lorem ipsum dolor sit amet, consectetur adipiscing elit. Non, dignissimos nihil unde.</p></div>
  <div class="service" style="left:223px"><div class="service-photo" role="img" aria-label="Children celebrating at a birthday party" style="background:radial-gradient(circle at 50% 40%,#e6c0a0,#3b7bc0)"></div><h3 class="script">Birthdays</h3><p>Lorem ipsum dolor sit amet, consectetur adipiscing elit. Non, dignissimos nihil unde.</p></div>
  <div class="service" style="left:349px"><div class="service-photo" role="img" aria-label="Model in a red dress on a runway" style="background:radial-gradient(circle at 50% 45%,#e04a2a,#4a120c)"></div><h3 class="script">Fashion shows</h3><p>Lorem ipsum dolor sit amet, consectetur adipiscing elit. Non, dignissimos nihil unde.</p></div>
  <div class="service" style="left:475px"><div class="service-photo" role="img" aria-label="Audience at a conference presentation" style="background:radial-gradient(circle at 50% 30%,#f2f2f0,#6a6f80)"></div><h3 class="script">Conferences</h3><p>Lorem ipsum dolor sit amet, consectetur adipiscing elit. Non, dignissimos nihil unde.</p></div>
  <span class="btn">KNOW MORE</span>
</section>

<section class="blog abs">
  <h2 class="section-title script">Our blog</h2>
  <svg class="ornament" width="92" height="6" viewBox="0 0 92 6"><path d="M0 3H36M56 3H92" stroke="#d8d4cf"/><circle cx="42" cy="3" r="2" fill="none" stroke="#bbb"/><circle cx="50" cy="3" r="2" fill="none" stroke="#bbb"/></svg>
  <article class="post" style="left:106px">
    <div class="post-photo" role="img" aria-label="Catering staff serving plated food" style="background:linear-gradient(135deg,#ece4da,#a58f7a)"><div class="date"><b>09</b><i>JUN, 2015</i></div></div>
    <h4>Lorem ipsum dolor sit amet, title consectetur</h4>
    <div class="meta">By Admin / 0 Comment / Wedding</div>
    <p>Lorem ipsum dolor sit amet, ut labore et dolore magna et sed aliqua et enim.</p>
    <div class="read"><span></span>Read More</div>
  </article>
  <article class="post" style="left:227px">
    <div class="post-photo" role="img" aria-label="Gold rings beside pink roses" style="background:linear-gradient(135deg,#f5f1ea,#e9c8bf)"><div class="date"><b>11</b><i>MAR, 2015</i></div></div>
    <h4>Lorem ipsum dolor sit amet, title consectetur</h4>
    <div class="meta">By Admin / 0 Comment / Event</div>
    <p>Lorem ipsum dolor sit amet, consectetur adipiscing tempor et enim.</p>
    <div class="read"><span></span>Read More</div>
  </article>
  <article class="post" style="left:348px">
    <div class="post-photo" role="img" aria-label="Close-up of coral roses" style="background:linear-gradient(135deg,#f08c74,#c8424a)"><div class="date"><b>12</b><i>JAN, 2015</i></div></div>
    <h4>Lorem ipsum dolor sit amet, title consectetur</h4>
    <div class="meta">By Admin / 2 Comment / Blog</div>
    <p>Lorem ipsum dolor sit amet, consectetur adipiscing tempor incididun</p>
    <div class="read"><span></span>Read More</div>
  </article>
  <article class="post" style="left:469px">
    <div class="post-photo" role="img" aria-label="Teacup beside a bouquet of flowers" style="background:linear-gradient(135deg,#c6b49a,#e8ecef)"><div class="date"><b>01</b><i>JAN, 2015</i></div></div>
    <h4>Lorem ipsum dolor sit amet, title consectetur</h4>
    <div class="meta">By Admin / 0 Comment / Blog</div>
    <p>dolor sit amet, consectetur adipiscing tempor incididunt ut labore et dolore magna et sed</p>
    <div class="read"><span></span>Read More</div>
  </article>
  <span class="btn">GO TO BLOG</span>
</section>

<footer class="site-footer abs">
  <div class="f-col f-about" style="left:112px">
    <h5><svg viewBox="0 0 11 6"><path d="M1 5C3 1 8 1 10 5" stroke="#999" fill="none"/></svg>ABOUT US</h5>
    <div class="f-brand"><span></span>Silver Fern Celebrations</div>
    <p>Lorem ipsum dolor sit amet, consectetur adipisicing elit. Quam culpa, hic autem itaque. Natus, ducimus quis. Iusto quaerat harum atque earum illum reprehenderit nisi quasi odit, optio iure officiis eaque.</p>
  </div>
  <div class="f-col" style="left:229px">
    <h5><svg viewBox="0 0 11 6"><path d="M1 5C3 1 8 1 10 5" stroke="#999" fill="none"/></svg>CATEGORIES</h5>
    <ul class="f-links"><li>Home</li><li>About us</li><li>Our services</li><li>Our blog</li><li>Contact</li></ul>
  </div>
  <div class="f-col f-info" style="left:349px">
    <h5><svg viewBox="0 0 11 6"><path d="M1 5C3 1 8 1 10 5" stroke="#999" fill="none"/></svg>INFO</h5>
    <ul>
      <li><svg viewBox="0 0 8 8"><circle cx="4" cy="4" r="3.3" fill="none" stroke="#8b1a8e"/><path d="M4 2V4H5.5" stroke="#8b1a8e" fill="none"/></svg>Monday – Friday (9:00am – 5:00pm)</li>
      <li><svg viewBox="0 0 8 8"><path d="M4 8C1 4.5 1 3 1 3A3 3 0 0 1 7 3C7 3 7 4.5 4 8Z" fill="#8b1a8e"/></svg>PO 1232 Your Road, M09 77 R<br>City - country</li>
      <li><svg viewBox="0 0 8 8"><path d="M0 4L8 0L5 8L4 5Z" fill="#8b1a8e"/></svg>maureen@silverferncelebrations.co.uk</li>
      <li><svg viewBox="0 0 8 8"><path d="M1 1L3 1L4 3L3 4C3.5 5 4 5.5 5 6L6 5L8 6V7.5C4 8 0 4 1 1Z" fill="#8b1a8e"/></svg>01632 960418 / 07700 900627</li>
    </ul>
  </div>
  <div class="f-col" style="left:472px">
    <h5><svg viewBox="0 0 11 6"><path d="M1 5C3 1 8 1 10 5" stroke="#999" fill="none"/></svg>SOCIAL</h5>
    <div class="social"><span></span><span></span><span></span><span></span><span></span></div>
    <p class="copyright">Copyright ©2015 Silver Fern Celebrations,<br>All rights reserved</p>
  </div>
</footer>

</body>
</html>
```